Envelope Design - Winner can do follow-up business

- Varnoko.com is a Swiss-based online store selling business shirts and accessories for business men
- Please visit the webpage to make yourself familiar with the company. Although the text is in German, with Plimbo translator you should be able to understand the main content.
- Our clients are mainly business men between 30 and 60 years old. Mostly with a high income working in the service industry (banking, insurance, lawyers, etc.). Sometimes there wives purchase the shirts for them ;-)
- The colors and the logo are given, as they are also used for the print materials (please see files in attachment)
- I am running several businesses and often need a talented web designer --> the winner gets substantial follow-up business
your task:
-for our company we need a new envelope design
-It should be simple and modern
-please use one of the logos in the followings.
-suprise me :)

```html
<!DOCTYPE html>
<html lang="en">
<head>
<meta charset="utf-8">
<title>Varnoko – Envelope Design</title>
<link rel="stylesheet" href="https://fonts.googleapis.com/css2?family=Quicksand:wght@400;500&family=Open+Sans:wght@400;600&display=swap">
<style>
  :root {
    --bg: #e9e9ea;
    --paper: #ffffff;
    --brand-red: #e31d16;
    --brand-yellow: #ecd865;
    --window-grey: #b3b3b3;
    --window-edge: #8f8f8f;
    --text-dark: #3a2a10;
    --pattern-pink: #f6d3d1;
    --pattern-cream: #f7f1d2;
  }
  * { margin: 0; padding: 0; box-sizing: border-box; }
  html, body { width: 1200px; height: 928px; overflow: hidden; background: var(--bg); }
  .canvas {
    width: 1200px; height: 928px;
    display: flex; flex-direction: column; align-items: center; justify-content: center;
    gap: 36px;
  }
  .envelope {
    width: 820px; height: 410px;
    background: var(--paper);
    box-shadow: 0 6px 18px rgba(0,0,0,0.12);
    display: block;
  }
  .logo-name {
    font-family: "Quicksand", sans-serif;
    font-weight: 400;
    font-size: 34px;
    letter-spacing: 6px;
    fill: var(--brand-yellow);
  }
  .contact-text {
    font-family: "Open Sans", sans-serif;
    font-size: 12px;
    font-weight: 600;
    fill: var(--text-dark);
  }
</style>
</head>
<body>
<main class="canvas">

  <!-- Front of envelope -->
  <svg class="envelope envelope-front" viewBox="0 0 820 410" aria-label="Envelope front">
    <defs>
      <linearGradient id="patternFill" x1="0" y1="0" x2="1" y2="1">
        <stop offset="0" stop-color="var(--pattern-pink)" stop-opacity="0.55"/>
        <stop offset="1" stop-color="var(--pattern-cream)" stop-opacity="0.8"/>
      </linearGradient>
    </defs>
    <rect class="decor-pattern" x="470" y="150" width="330" height="240" fill="url(#patternFill)" role="img" aria-label="Faint decorative pattern of small squares and stripes"/>

    <g class="logo">
      <rect x="52" y="34" width="26" height="26" fill="var(--brand-yellow)"/>
      <text class="logo-name" x="90" y="60">VARNOKO</text>
    </g>

    <rect class="address-window" x="72" y="108" width="330" height="170" rx="22" fill="var(--window-grey)" stroke="var(--window-edge)" stroke-width="2"/>

    <g class="bottom-band">
      <rect x="0" y="320" width="820" height="3" fill="var(--brand-red)"/>
      <rect x="0" y="323" width="820" height="42" fill="var(--brand-yellow)"/>
      <rect x="0" y="365" width="820" height="3" fill="var(--brand-red)"/>
    </g>
  </svg>

  <!-- Back of envelope -->
  <svg class="envelope envelope-back" viewBox="0 0 820 410" aria-label="Envelope back">
    <defs>
      <linearGradient id="patternFillBack" x1="0" y1="0" x2="1" y2="1">
        <stop offset="0" stop-color="var(--pattern-pink)" stop-opacity="0.55"/>
        <stop offset="1" stop-color="var(--pattern-cream)" stop-opacity="0.8"/>
      </linearGradient>
    </defs>
    <rect class="decor-pattern" x="20" y="20" width="300" height="230" fill="url(#patternFillBack)" role="img" aria-label="Faint decorative pattern of small squares and stripes"/>

    <path class="flap" d="M150 0 H820 V255 Q810 285 780 280 L190 70 Q150 50 150 20 Z" fill="var(--brand-red)"/>

    <g class="contact-band">
      <rect x="0" y="300" width="820" height="3" fill="var(--brand-red)"/>
      <rect x="0" y="303" width="820" height="56" fill="var(--brand-yellow)"/>
      <rect x="0" y="359" width="820" height="3" fill="var(--brand-red)"/>
    </g>

    <g class="contact-left">
      <rect x="26" y="315" width="8" height="8" fill="var(--brand-red)"/>
      <text class="contact-text" x="42" y="323">Varnoko GmbH</text>
      <path d="M30 334 a4 4 0 0 1 4 4 c0 3 -4 7 -4 7 c0 0 -4 -4 -4 -7 a4 4 0 0 1 4 -4 z" fill="var(--brand-red)"/>
      <text class="contact-text" x="42" y="344">Lindenweg 14, 8700 Uferstadt</text>
    </g>

    <g class="contact-right">
      <path d="M608 315 h3 l2 4 l-2 1 a8 8 0 0 0 3 3 l1 -2 l4 2 v3 a2 2 0 0 1 -2 1 a12 12 0 0 1 -10 -10 a2 2 0 0 1 1 -2 z" fill="var(--brand-red)"/>
      <text class="contact-text" x="628" y="325">+41 44 555 10 20</text>
      <rect x="608" y="336" width="12" height="9" fill="var(--brand-red)"/>
      <text class="contact-text" x="628" y="345">hello@varnoko.com</text>
    </g>
  </svg>

</main>
</body>
</html>
```